TuneRoost - Music Industry App needs a top quality wordpress homepage

We need a modern responsive wordpress homepage built. Our website will only feature one page with the goal to get people to sign up to our app. A word document has been uploaded outlining the page content/sections.

Once the homepage is finalised, I will also need 2 landing pages built as part of this competition. It will be very similar to the homepage with the same layout etc but just feature different images and content. The homepage is for anyone (artists and venues) to find out about us but the landing pages will be artist or venue specific.

The completed work must be delivered as an exportable file into wordpress and be designed properly so no more work is needed to begin utilising as the actual website. The images used must be setup correctly for speed and quality also.

Target Market(s)

Venues and Artists.

Coding

Coded - Design and coding required

Requirements
Must have
• UPDATE: High Res Logo files attached
• Must be a modern looking website and be responsive. Must look good across all devices from desktop, to mobile and tablet. Needs to be very high quality.
• Please see the attached logo - I am waiting for the final high quality version and will reupload when complete but this will be enough to get you started for now. The website must have a dark base colour and have red/white elements to match the logo. The red colour used MUST match the red colour used in the logo.
• Please have a go at creating it how you think is best and provide feedback from there. I am leaving it very open to the designers so I can get the best website possible and lots of different ideas etc.

```html
<!DOCTYPE html>
<html lang="en">
<head>
<meta charset="utf-8">
<title>TuneRoost – Book Live Music</title>
<link rel="stylesheet" href="https://fonts.googleapis.com/css2?family=Montserrat:wght@500;600&family=Open+Sans:wght@300;400;600;700&family=Ubuntu:wght@500;700&display=swap">
<style>
:root{
  --red:#e1000f;
  --red-dark:#a8000b;
  --black:#000;
  --ink:#0c0c0c;
  --white:#fff;
  --grey:#d8d8d8;
  --sans:"Open Sans",sans-serif;
  --nav:"Montserrat",sans-serif;
  --head:"Ubuntu",sans-serif;
}
*{box-sizing:border-box;margin:0;padding:0}
html,body{width:1200px;height:4425px;overflow:hidden;background:var(--black);color:var(--white);font-family:var(--sans)}
.page{position:relative;width:1200px;height:4425px;overflow:hidden}
.abs{position:absolute}
.layer-bg{z-index:1}
.layer-shape{z-index:2}
.layer-content{z-index:3}

/* header */
.brand{left:115px;top:30px;display:flex;align-items:center;gap:12px;font-family:var(--nav);font-weight:600;font-size:30px}
.brand-dot{width:22px;height:22px;border-radius:50%;background:var(--red)}
.btn{display:flex;align-items:center;justify-content:center;font-family:var(--nav);font-weight:600;font-size:14px;letter-spacing:.3px;text-transform:uppercase;color:var(--white)}
.btn-solid{background:var(--red)}
.btn-outline{border:1.5px solid var(--red)}
.btn-quote{left:633px;top:20px;width:214px;height:45px}
.btn-join{left:874px;top:20px;width:214px;height:45px}
.nav{left:440px;top:85px;display:flex;gap:36px;font-family:var(--nav);font-weight:600;font-size:14px}

/* hero */
.hero-photo{left:0;top:130px;width:1200px;height:590px;background:radial-gradient(circle at 20% 20%,#4b2a6a 0,transparent 40%),radial-gradient(circle at 55% 25%,#8a2a35 0,transparent 35%),radial-gradient(circle at 85% 40%,#1f6a52 0,transparent 40%),linear-gradient(180deg,#2a2230,#141414)}
.hero-title{left:0;top:280px;width:1200px;text-align:center;font-weight:700;font-size:66px;letter-spacing:.5px}
.hero-sub{left:0;top:358px;width:1200px;text-align:center;font-size:22px}
.signup{left:220px;top:407px;display:flex;height:50px}
.signup-field{width:520px;background:var(--white);color:#555;font-size:14px;display:flex;align-items:center;padding-left:20px}
.signup-btn{width:240px;font-family:var(--nav);font-size:15px}
.play{left:572px;top:482px;width:56px;height:56px;border-radius:50%;background:var(--red);box-shadow:0 0 18px 6px rgba(225,0,15,.6)}
.arrow{top:316px}

/* how */
.section-title{font-weight:300;font-size:44px;text-align:center}
.how-title{left:0;top:812px;width:1200px}
.step{top:908px;width:200px;text-align:center;font-size:16px;line-height:26px;color:var(--grey)}
.step-icon{width:124px;height:124px;margin:0 auto 22px;border-radius:50%;background:var(--red);display:flex;align-items:center;justify-content:center;box-shadow:0 0 0 6px rgba(225,0,15,.25),0 0 24px 6px rgba(225,0,15,.55)}

/* why */
.why-photo{left:105px;top:1425px;width:420px;height:420px;border-radius:52% 48% 44% 56% / 48% 56% 44% 52%;background:radial-gradient(circle at 45% 40%,#5b4a30,#1a1410 60%,#050505);box-shadow:0 0 0 4px #111}
.why-title{left:597px;top:1368px;font-family:var(--head);font-weight:700;font-size:36px}
.why-item{left:600px;display:flex;gap:20px;width:450px}
.why-icon{flex:none;width:56px;height:56px;border-radius:50%;background:var(--white);display:flex;align-items:center;justify-content:center}
.why-item h3{font-family:var(--head);font-weight:500;font-size:21px;margin-top:-4px}
.why-item p{font-size:13.5px;line-height:21px;margin-top:4px}

/* venues & artists */
.role-photo{width:200px;height:200px;border-radius:50%;border:3px solid var(--red)}
.venue-photo{left:209px;top:2057px;background:radial-gradient(circle at 60% 40%,#6f4fd0,#c01060 45%,#2a0620 80%)}
.artist-photo{left:752px;top:2057px;background:radial-gradient(circle at 50% 35%,#c9ccd4,#5a5f6a 40%,#121418 80%)}
.role-title{top:2275px;width:400px;text-align:center}
.perks{list-style:none;width:480px;font-size:14px;line-height:29px}
.perks li{position:relative;padding-left:40px}
.perks li svg{position:absolute;left:0;top:7px}
.note{left:110px;top:2606px;width:500px;font-size:14px;line-height:29px}
.cta{top:2725px;width:285px;height:54px;font-size:15px}

/* about */
.about-title{left:113px;top:3098px;font-family:var(--head);font-weight:700;font-size:40px}
.about-copy{left:113px;top:3162px;width:450px;font-size:15px;line-height:29px}
.read-more{left:113px;top:3435px;width:155px;height:50px;border:1.5px solid var(--white);font-size:16px}
.about-photo{left:660px;top:3005px;width:425px;height:420px;border-radius:46% 54% 50% 50% / 52% 46% 54% 48%;background:radial-gradient(circle at 40% 35%,#4aa6e0,#14408a 45%,#061536 85%)}

/* contact */
.map{left:0;top:3560px;width:597px;height:600px;background:linear-gradient(135deg,#ece9e1,#dcdad2 55%,#c9dbe8)}
.contact-photo{left:597px;top:3500px;width:603px;height:660px;background:radial-gradient(circle at 80% 30%,#3a2e24,#17120e 55%,#050505)}
.contact-title{left:667px;top:3664px;font-family:var(--head);font-weight:700;font-size:38px}
.contact-row{left:667px;display:flex;gap:26px;align-items:center;font-size:15px;line-height:24px}
.contact-icon{width:56px;height:56px;border-radius:50%;border:1.5px solid var(--white);display:flex;align-items:center;justify-content:center;flex:none}

/* footer */
.social{left:491px;top:4251px;display:flex;gap:11px}
.social span{width:48px;height:48px;border-radius:50%;border:2px solid var(--red)}
.foot-nav{left:0;top:4336px;width:1200px;display:flex;justify-content:center;gap:26px;font-size:13.5px}
.foot-nav i{font-style:normal;color:#888}
.copy{left:0;top:4372px;width:1200px;text-align:center;font-size:13px}
</style>
</head>
<body>
<div class="page">

  <!-- backgrounds -->
  <div class="abs layer-bg hero-photo" role="img" aria-label="Live band performing on a smoky stage with coloured lights"></div>
  <div class="abs layer-bg contact-photo" role="img" aria-label="Singer with guitar at a microphone in a dark room"></div>
  <div class="abs layer-bg map" role="img" aria-label="Street map showing the office location"></div>

  <!-- bands and waves -->
  <svg class="abs layer-shape" style="left:0;top:0" width="1200" height="4425" viewBox="0 0 1200 4425" aria-hidden="true">
    <rect x="0" y="0" width="1200" height="130" fill="#000"/>
    <path d="M0 560C300 600 480 665 700 645C900 625 1050 560 1200 540L1200 720L0 720Z" fill="var(--red)"/>
    <path d="M0 605C250 595 440 695 650 703C860 712 1010 640 1200 600L1200 760L0 760Z" fill="#000"/>
    <circle cx="180" cy="2620" r="420" fill="#0b0b0b"/>
    <circle cx="1050" cy="2500" r="400" fill="#0b0b0b"/>
    <path d="M0 1300C320 1340 720 1195 1200 1225L1200 1852C900 1880 420 1985 0 1955Z" fill="var(--red)"/>
    <path d="M0 1312C320 1352 720 1208 1200 1238" stroke="var(--red-dark)" stroke-width="3" fill="none"/>
    <path d="M0 1943C420 1972 900 1868 1200 1840" stroke="var(--red-dark)" stroke-width="3" fill="none"/>
    <path d="M0 2950C320 2995 720 2880 1200 2890L1200 3520C820 3530 480 3560 0 3600Z" fill="var(--red)"/>
    <path d="M0 2962C320 3007 720 2892 1200 2902" stroke="var(--red-dark)" stroke-width="3" fill="none"/>
  </svg>

  <!-- header -->
  <div class="abs layer-content brand"><span class="brand-dot"></span>TuneRoost</div>
  <div class="abs layer-content btn btn-solid btn-quote">Get the quote</div>
  <div class="abs layer-content btn btn-outline btn-join">Join TuneRoost</div>
  <nav class="abs layer-content nav"><span>HOME</span><span>HOW IT WORKS</span><span>VENUES AND ARTIST</span><span>ABOUT US</span><span>FAQ'S</span><span>BLOG</span></nav>

  <!-- hero -->
  <h1 class="abs layer-content hero-title">RIDEO FOR LIVE MUSIC</h1>
  <p class="abs layer-content hero-sub">'TuneRoost connects venues with artists to make booking gigs simple'</p>
  <div class="abs layer-content signup"><div class="signup-field">Enter the email address</div><div class="btn btn-solid signup-btn">SIGN UP NOW FOR FREE</div></div>
  <div class="abs layer-content play"><svg width="56" height="56" viewBox="0 0 56 56"><path d="M23 19L36 28L23 37Z" fill="#fff"/></svg></div>
  <svg class="abs layer-content arrow" style="left:88px" width="24" height="44" viewBox="0 0 24 44"><path d="M20 4L4 22L20 40" stroke="#fff" stroke-width="6" fill="none"/></svg>
  <svg class="abs layer-content arrow" style="left:1136px" width="24" height="44" viewBox="0 0 24 44"><path d="M4 4L20 22L4 40" stroke="#fff" stroke-width="6" fill="none"/></svg>

  <!-- how it works -->
  <h2 class="abs layer-content section-title how-title">How TuneRoost Works</h2>
  <div class="abs layer-content step" style="left:88px">
    <div class="step-icon"><svg width="44" height="44" viewBox="0 0 44 44" fill="none" stroke="#fff" stroke-width="2.5"><rect x="9" y="6" width="24" height="32" rx="2"/><path d="M14 15H28M14 21H28M14 27H24M30 4L36 10L26 20"/></svg></div>
    Artists and venues sign up for free and create a profile</div>
  <div class="abs layer-content step" style="left:291px">
    <div class="step-icon"><svg width="44" height="44" viewBox="0 0 44 44" fill="#fff"><circle cx="14" cy="30" r="6"/><rect x="18" y="8" width="3" height="22"/><path d="M21 8C27 10 30 14 29 20C27 16 24 15 21 15Z"/><rect x="26" y="30" width="14" height="3"/><rect x="26" y="35" width="14" height="3"/></svg></div>
    Venues search for an artist for their upcoming gigs</div>
  <div class="abs layer-content step" style="left:490px">
    <div class="step-icon"><svg width="44" height="44" viewBox="0 0 44 44" fill="none" stroke="#fff" stroke-width="2.5"><circle cx="22" cy="22" r="17"/><path d="M16 13C14 15 14 19 18 24C22 29 26 31 29 29L30 27L26 24L24 26C22 25 19 22 18 20L20 18L17 13Z"/></svg></div>
    Venues request a quote and communicate with the artist direct</div>
  <div class="abs layer-content step" style="left:694px">
    <div class="step-icon"><svg width="44" height="44" viewBox="0 0 44 44" fill="none" stroke="#fff" stroke-width="2.5"><path d="M4 14H20L26 18H16M4 14V24H12L22 28"/><circle cx="30" cy="26" r="9"/><path d="M30 21V31M27 23H32M28 29H33"/></svg></div>
    The gig is booked in once payment is provided by the venue.</div>
  <div class="abs layer-content step" style="left:895px">
    <div class="step-icon"><svg width="44" height="44" viewBox="0 0 44 44" fill="none" stroke="#fff" stroke-width="2.5"><circle cx="26" cy="22" r="14"/><path d="M26 13V22L32 26M4 18H10M2 24H10M6 30H12"/></svg></div>
    Upon completion the money is paid to the artist within 48 hours or less.</div>

  <!-- why -->
  <div class="abs layer-content why-photo" role="img" aria-label="Drummer playing a kit under sparkling stage lights"></div>
  <h2 class="abs layer-content why-title">Why TuneRoost?</h2>
  <div class="abs layer-content why-item" style="top:1447px">
    <div class="why-icon"><svg width="28" height="28" viewBox="0 0 28 28" fill="var(--red)"><rect x="4" y="6" width="20" height="3"/><rect x="10" y="12" width="14" height="3"/><rect x="10" y="18" width="14" height="3"/><circle cx="6" cy="19" r="3"/><rect x="8" y="10" width="2" height="9"/></svg></div>
    <div><h3>Simple</h3><p>TuneRoost makes gig booking easy for both the venue and artist.</p></div></div>
  <div class="abs layer-content why-item" style="top:1542px">
    <div class="why-icon"><svg width="30" height="30" viewBox="0 0 30 30" fill="var(--red)" stroke="var(--red)" stroke-width="2"><circle cx="15" cy="15" r="3.5"/><circle cx="6" cy="6" r="3"/><circle cx="24" cy="6" r="3"/><circle cx="5" cy="22" r="3"/><circle cx="25" cy="22" r="3"/><circle cx="15" cy="27" r="2.5"/><path d="M15 15L6 6M15 15L24 6M15 15L5 22M15 15L25 22M15 15V27"/></svg></div>
    <div><h3>Connect</h3><p>Join the TuneRoost community which is full of amazing artists and venues.</p></div></div>
  <div class="abs layer-content why-item" style="top:1637px">
    <div class="why-icon"><svg width="28" height="30" viewBox="0 0 28 30" fill="none" stroke="var(--red)" stroke-width="3"><path d="M14 3L25 7V15C25 21 20 25 14 27C8 25 3 21 3 15V7Z"/><path d="M14 9V21"/></svg></div>
    <div><h3>Protection</h3><p>Everyone is protected with our complimentary dispute resolutions.</p></div></div>
  <div class="abs layer-content why-item" style="top:1732px">
    <div class="why-icon"><svg width="28" height="30" viewBox="0 0 28 30" fill="none" stroke="var(--red)" stroke-width="3.5"><path d="M14 2V28M20 8C17 5 8 5 8 10C8 16 20 13 20 20C20 25 10 25 7 22"/></svg></div>
    <div><h3>Price</h3><p>Get the best rate possible with TuneRoost only receiving 5% of the artists fee</p></div></div>

  <!-- venues & artists -->
  <div class="abs layer-content role-photo venue-photo" role="img" aria-label="Singer under pink and blue club lights"></div>
  <div class="abs layer-content role-photo artist-photo" role="img" aria-label="Guitarist standing in stage smoke"></div>
  <h2 class="abs layer-content section-title role-title" style="left:109px">Venues</h2>
  <h2 class="abs layer-content section-title role-title" style="left:652px">Artists</h2>

  <ul class="abs layer-content perks" style="left:112px;top:2345px">
    <li><svg width="20" height="16" viewBox="0 0 20 16" fill="none" stroke="#fff" stroke-width="1.6"><path d="M1 2H13M1 6H13M1 10H8M1 14H8"/><circle cx="14" cy="13" r="2.5"/><path d="M16.5 13V5L19 6"/></svg>TuneRoost is a 100% FREE service for all venues - you pay us nothing!</li>
    <li><svg width="20" height="16" viewBox="0 0 20 16" fill="none" stroke="#fff" stroke-width="1.6"><path d="M1 2H13M1 6H13M1 10H8M1 14H8"/><circle cx="14" cy="13" r="2.5"/><path d="M16.5 13V5L19 6"/></svg>Get instant access to hundreds of artists around your local community</li>
    <li><svg width="20" height="16" viewBox="0 0 20 16" fill="none" stroke="#fff" stroke-width="1.6"><path d="M1 2H13M1 6H13M1 10H8M1 14H8"/><circle cx="14" cy="13" r="2.5"/><path d="M16.5 13V5L19 6"/></svg>All genres to suit any venue from a pub to a wedding or even a nightclub</li>
    <li><svg width="20" height="16" viewBox="0 0 20 16" fill="none" stroke="#fff" stroke-width="1.6"><path d="M1 2H13M1 6H13M1 10H8M1 14H8"/><circle cx="14" cy="13" r="2.5"/><path d="M16.5 13V5L19 6"/></svg>Simple booking process with a money back guarantee</li>
    <li><svg width="20" height="16" viewBox="0 0 20 16" fill="none" stroke="#fff" stroke-width="1.6"><path d="M1 2H13M1 6H13M1 10H8M1 14H8"/><circle cx="14" cy="13" r="2.5"/><path d="M16.5 13V5L19 6"/></svg>Communicate directly with the artist and negotiate the price</li>
  </ul>
  <ul class="abs layer-content perks" style="left:655px;top:2345px">
    <li><svg width="20" height="16" viewBox="0 0 20 16" fill="none" stroke="#fff" stroke-width="1.6"><path d="M1 2H13M1 6H13M1 10H8M1 14H8"/><circle cx="14" cy="13" r="2.5"/><path d="M16.5 13V5L19 6"/></svg>Sign up to TuneRoost for FREE and get yourself in front of venues</li>
    <li><svg width="20" height="16" viewBox="0 0 20 16" fill="none" stroke="#fff" stroke-width="1.6"><path d="M1 2H13M1 6H13M1 10H8M1 14H8"/><circle cx="14" cy="13" r="2.5"/><path d="M16.5 13V5L19 6"/></svg>Only pay us if you get a gig - we only get 5% of the fee you charge the venue</li>
    <li><svg width="20" height="16" viewBox="0 0 20 16" fill="none" stroke="#fff" stroke-width="1.6"><path d="M1 2H13M1 6H13M1 10H8M1 14H8"/><circle cx="14" cy="13" r="2.5"/><path d="M16.5 13V5L19 6"/></svg>All genres and artists welcome - as long as you're experienced and professional</li>
    <li><svg width="20" height="16" viewBox="0 0 20 16" fill="none" stroke="#fff" stroke-width="1.6"><path d="M1 2H13M1 6H13M1 10H8M1 14H8"/><circle cx="14" cy="13" r="2.5"/><path d="M16.5 13V5L19 6"/></svg>Get paid within 48 hours or less after the gig guaranteed!</li>
    <li><svg width="20" height="16" viewBox="0 0 20 16" fill="none" stroke="#fff" stroke-width="1.6"><path d="M1 2H13M1 6H13M1 10H8M1 14H8"/><circle cx="14" cy="13" r="2.5"/><path d="M16.5 13V5L19 6"/></svg>Negotiate your price and don't pay huge agent fees to ensure you earn top dollar</li>
  </ul>
  <p class="abs layer-content note">TuneRoost is not yet ready to host gigs as we're currently working on building our artists. We are launching for venues in Q4 2019. Pre-register now to keep informed and be one of the first people to use our platform.</p>
  <div class="abs layer-content btn btn-solid cta" style="left:167px">EMAIL INPUT TO PRE REGISTER</div>
  <div class="abs layer-content btn btn-solid cta" style="left:710px">SIGN UP TO TUNEROOST FOR FREE</div>

  <!-- about -->
  <h2 class="abs layer-content about-title">About TuneRoost</h2>
  <p class="abs layer-content about-copy">Lorem ipsum dolor sit amet, consectetur adipiscing elit, sed do eiusmod tempor incididunt ut labore et dolore magna aliqua. Ut enim ad minim veniam, quis nostrud exercitation ullamco laboris nisi ut aliquip ex ea commodo consequat. Duis aute irure dolor in reprehenderit in voluptate velit esse cillum dolore eu fugiat nulla pariatur. Excepteur sint occaecat cupidatat non proident, sunt in culpa qui officia deserunt mollit anim id est laborum</p>
  <div class="abs layer-content btn read-more">READ MORE</div>
  <div class="abs layer-content about-photo" role="img" aria-label="Singer and guitarist performing together under blue lights"></div>

  <!-- contact -->
  <h2 class="abs layer-content contact-title">Contact Us</h2>
  <div class="abs layer-content contact-row" style="top:3762px">
    <div class="contact-icon"><svg width="22" height="16" viewBox="0 0 22 16" fill="#fff"><path d="M0 0H22V2L11 9L0 2Z"/><path d="M0 4L11 11L22 4V16H0Z"/></svg></div>
    <div>Email Us :<br>hello@tuneroost.com</div></div>
  <div class="abs layer-content contact-row" style="top:3847px">
    <div class="contact-icon"><svg width="22" height="22" viewBox="0 0 22 22" fill="#fff"><path d="M4 2L8 2L10 7L7 9C8 12 10 14 13 15L15 12L20 14V18C20 19 19 20 18 20C9 20 2 13 2 4C2 3 3 2 4 2Z"/></svg></div>
    <div>Phone :<br>555-214-0387</div></div>
  <div class="abs layer-content contact-row" style="top:3930px">
    <div class="contact-icon"><svg width="18" height="24" viewBox="0 0 18 24" fill="#fff"><path d="M9 0C4 0 0 4 0 9C0 15 9 24 9 24C9 24 18 15 18 9C18 4 14 0 9 0ZM9 13A4 4 0 1 1 9 5A4 4 0 0 1 9 13Z"/></svg></div>
    <div>Address :<br>P.O. Box 4120<br>Riverton, OR 97100</div></div>

  <!-- footer -->
  <div class="abs layer-content social" aria-label="Social links"><span></span><span></span><span></span><span></span></div>
  <nav class="abs layer-content foot-nav"><span>Home</span><i>|</i><span>How It Works</span><i>|</i><span>venues and artist</span><i>|</i><span>About Us</span><i>|</i><span>Faq's</span><i>|</i><span>Blog</span></nav>
  <p class="abs layer-content copy">Copyrights © 2019,The Company Name. All rights reserved.Terms &amp; Services</p>

</div>
</body>
</html>
```